Under Morning Lantern website

I need a website to sell my t-shirt designs. I have around 5 designs I plan to sell on my initial launch, but only 3 photos at the moment. I would love a main page with the product images below maybe a large nicely designed header image, showing products with their sizes, item name/description, a way to add to cart and a review system like stars below each product image. Maybe a share option to Snapshot, Friendbook, Chirper, Pinterest, etc. would be cool too. Also on the main page under the product images a section showcasing my Snapshot photos for the company. Then a section where I will include an About Me video from like Reelhub. Lastly, on the main page an option to join my Mailing List at the footer with links to my Friendbook and Snapshot social accounts, links to pages (About Me, Shop, Snapshot page, & Contact Us) as well as Track Order.

The other 4 pages will be for an About Me, which is the video I will make later that will be from Reelhub. Then the Shop page. Then the Snapshot page showcasing all the photos I plan to use to market the products, and a Contact Us Page.

I plan to possibly connect this to Shopify, so showcasing payment options (Palo, Birch Pay, Wayfarer, etc.) would be nice.

Lastly, I don't plan on doing returns/exchanges so maybe an area showing that would be nice too. ALL SALES FINAL

Mobile Friendly!

1st image is logo and other 4 images are t-shirt designs

Coded - Design and coding required

5+ page

• Separate pages, No Refunds (All Sales Final), Add to Cart, Way to Purchase

```html
<!DOCTYPE html>
<html lang="en">
<head>
<meta charset="utf-8">
<title>Under Morning Lantern — Shop</title>
<link href="https://fonts.googleapis.com/css2?family=Poppins:wght@300;400;500;600;700&family=Roboto:wght@300;400;500;700;900&display=swap" rel="stylesheet">
<style>
:root{
  --brand:#03a9ec;
  --ink:#1f1f1f;
  --muted:#8a8a8a;
  --line:#e3e3e3;
  --star:#f5a100;
  --hover-bg:#eef8fd;
  --footer:#2b2b2b;
  --footer-text:#b9b9b9;
  --white:#ffffff;
}
*{box-sizing:border-box;margin:0;padding:0}
html,body{width:1200px;height:2480px;overflow:hidden;background:var(--white)}
body{position:relative;font-family:"Roboto",sans-serif;color:var(--ink)}
.abs{position:absolute}

/* header */
.hero{position:absolute;left:0;top:0;width:1200px;height:314px;background:var(--brand)}
.brand{position:absolute;left:117px;top:40px;color:#111;font-family:"Roboto",sans-serif;font-weight:900;font-size:44px;letter-spacing:1px;line-height:1}
.brand small{display:block;font-size:8px;font-weight:700;letter-spacing:2.6px;color:var(--white);margin-top:4px;padding-left:16px}
.nav{position:absolute;left:428px;top:47px;width:344px;height:41px;background:var(--white);border-radius:21px;display:flex;align-items:center;justify-content:space-around;padding:0 18px;font-size:14px;color:#666}
.nav .active{color:#111;font-weight:500;position:relative}
.nav .active::after{content:"";position:absolute;left:50%;bottom:-7px;width:4px;height:4px;margin-left:-2px;border-radius:50%;background:#111}
.track{position:absolute;left:953px;top:59px;color:var(--white);font-size:14px}
.cart{position:absolute;left:1049px;top:55px}
.cart-badge{position:absolute;left:1065px;top:48px;width:16px;height:16px;border-radius:50%;background:#111;color:var(--white);font-size:10px;text-align:center;line-height:16px}
.hero h1{position:absolute;top:198px;width:1200px;text-align:center;color:var(--white);font-family:"Roboto",sans-serif;font-weight:700;font-size:36px}
.crumbs{position:absolute;top:248px;width:1200px;text-align:center;color:var(--white);font-size:16px}
.crumbs span{margin:0 14px}

/* filter */
.filters{position:absolute;left:122px;top:357px;width:940px;display:flex;align-items:center;font-size:16px}
.filters .label{margin-right:16px}
.filters .opt{margin-right:30px;display:flex;align-items:center;gap:6px}
.filters .opt i{font-style:normal;font-size:10px;color:#999}
.filters .count{color:#999;margin-left:16px}
.filters .sort{margin-left:auto}

/* products */
.card{position:absolute;width:221px;height:323px;border:1px solid var(--line);background:var(--white)}
.card.is-hover{background:var(--hover-bg);border-color:var(--brand);box-shadow:0 4px 14px rgba(3,169,236,.12)}
.shot{position:absolute;left:36px;top:30px;width:150px;height:170px;border-radius:6px}
.shot.black{background:linear-gradient(160deg,#2b2b2b,#0c0c0c)}
.shot.white{background:linear-gradient(160deg,#f2f2f2,#cfcfcf)}
.shot.teal{background:linear-gradient(160deg,#3fc7b8,#27a497)}
.shot.pair-white{background:linear-gradient(120deg,#1a1a1a 0 45%,#dcdcdc 45%)}
.shot.pair-purple{background:linear-gradient(120deg,#1a1a1a 0 45%,#8a5cc9 45%)}
.pname{position:absolute;left:35px;top:224px;font-family:"Poppins",sans-serif;font-weight:500;font-size:16px}
.stars{position:absolute;left:35px;top:246px;color:var(--star);font-size:13px;letter-spacing:1px}
.price{position:absolute;left:35px;top:270px;font-family:"Poppins",sans-serif;font-weight:600;font-size:17px}
.tools{position:absolute;right:16px;top:24px;display:flex;flex-direction:column;gap:14px}
.tool{width:40px;height:40px;border-radius:50%;border:1.5px solid var(--brand);background:var(--white);display:flex;align-items:center;justify-content:center}
.tool.fill{background:var(--brand)}

/* pagination */
.pager{position:absolute;top:1506px;left:470px;display:flex;gap:9px}
.pg{width:35px;height:35px;border-radius:50%;border:1.5px solid #bde4f5;color:#999;font-size:15px;display:flex;align-items:center;justify-content:center}
.pg.nav-btn{border-color:#6cc7ee}
.pg.current{background:var(--brand);border-color:var(--brand);color:var(--white)}

/* gallery */
.gallery-title{position:absolute;left:272px;top:1603px;font-family:"Poppins",sans-serif;font-weight:600;font-size:30px;color:#333}
.gallery-lede{position:absolute;left:272px;top:1647px;width:680px;font-family:"Poppins",sans-serif;font-size:16px;line-height:21px;color:#333}
.photo{position:absolute}

/* newsletter */
.news-title{position:absolute;top:2056px;width:1200px;text-align:center;font-family:"Poppins",sans-serif;font-weight:400;font-size:34px;color:#222}
.news-sub{position:absolute;top:2104px;width:1200px;text-align:center;font-family:"Poppins",sans-serif;font-weight:300;font-size:12px;color:#555}
.news-field{position:absolute;left:261px;top:2153px;width:677px;height:25px;border-bottom:1px solid #cfcfcf;display:flex;justify-content:space-between;font-family:"Poppins",sans-serif;font-size:10px}
.news-field .ph{color:#c4c4c4}
.news-field .btn{color:#9a9a9a;font-weight:500}

/* footer */
.footer{position:absolute;left:0;top:2234px;width:1200px;height:246px;background:var(--footer);color:var(--footer-text)}
.fcol{position:absolute;top:44px;font-size:14px}
.fcol h4{font-weight:400;font-size:16px;color:#e6e6e6;margin-bottom:18px}
.fcol p{line-height:23px;margin-bottom:10px}
.fcol ul{list-style:none}
.fcol li{line-height:24.5px}
.fdiv{position:absolute;top:44px;width:1px;height:145px;background:#3d3d3d}
.fbrand{position:absolute;left:860px;top:70px;width:154px;text-align:center;color:var(--brand);font-weight:900;font-size:36px;line-height:1}
.fbrand small{display:block;font-size:7px;letter-spacing:2px;color:#ddd;font-weight:700;margin-top:3px}
.social{position:absolute;left:852px;top:150px;width:170px;display:flex;justify-content:space-between;font-size:11px;color:#aaa}
</style>
</head>
<body>

<header class="hero">
  <div class="brand">U.M.L.<small>UNDER MORNING LANTERN</small></div>
  <nav class="nav"><span>About</span><span class="active">Shop</span><span>Snapshot</span><span>Contact</span></nav>
  <div class="track">Track Order</div>
  <svg class="cart" width="26" height="24" viewBox="0 0 26 24" fill="none" stroke="#fff" stroke-width="1.8" stroke-linecap="round" stroke-linejoin="round"><path d="M1 2h4l3 13h13l3-9H7"/><circle cx="10" cy="20" r="1.8"/><circle cx="19" cy="20" r="1.8"/></svg>
  <div class="cart-badge">0</div>
  <h1>SHOP PAGE</h1>
  <div class="crumbs">Home<span>|</span>Shop</div>
</header>

<section class="filters">
  <span class="label">Filter by:</span>
  <span class="opt"><svg width="16" height="18" viewBox="0 0 16 18" fill="none" stroke="#bbb" stroke-width="1.2"><rect x="1.5" y="2.5" width="13" height="14" rx="1"/><path d="M5 2.5V1h6v1.5M4 7h8M4 10h8M4 13h5"/></svg>&nbsp;Categories</span>
  <span class="opt">Colors <i>⌄</i></span>
  <span class="opt">Sizes <i>⌄</i></span>
  <span class="opt">Price <i>⌄</i></span>
  <span class="count">20 results</span>
  <span class="sort">Default Sorting</span>
</section>

<main class="products">
  <article class="card" style="left:119px;top:424px"><div class="shot black" role="img" aria-label="Black tee with lettered front print"></div><div class="pname">Product Name</div><div class="stars">★★★☆☆</div><div class="price">$120.00</div></article>
  <article class="card is-hover" style="left:366px;top:424px"><div class="shot black" role="img" aria-label="Black tee with blue chest wordmark"></div>
    <div class="tools">
      <span class="tool"><svg width="16" height="16" viewBox="0 0 16 16" fill="none" stroke="#333" stroke-width="1.3"><path d="M2 6V2h4M2 2l5 5M14 10v4h-4M14 14l-5-5M10 2h4v4M14 2L9 7M6 14H2v-4M2 14l5-5"/></svg></span>
      <span class="tool"><svg width="16" height="15" viewBox="0 0 16 15" fill="none" stroke="#333" stroke-width="1.3"><path d="M8 13.5S1.5 9.5 1.5 5A3.3 3.3 0 0 1 8 3.5 3.3 3.3 0 0 1 14.5 5C14.5 9.5 8 13.5 8 13.5z"/></svg></span>
      <span class="tool fill"><svg width="16" height="15" viewBox="0 0 26 24" fill="none" stroke="#fff" stroke-width="2.4" stroke-linecap="round"><path d="M1 2h4l3 13h13l3-9H7"/><circle cx="10" cy="20" r="1.8"/><circle cx="19" cy="20" r="1.8"/></svg></span>
    </div>
    <div class="pname">Product Name</div><div class="stars">★★★★☆</div><div class="price">$120.00</div></article>
  <article class="card" style="left:613px;top:424px"><div class="shot white" role="img" aria-label="Two white tees with heart print"></div><div class="pname">Product Name</div><div class="stars">★★★★★</div><div class="price">$120.00</div></article>
  <article class="card" style="left:860px;top:424px"><div class="shot black" role="img" aria-label="Black tee with purple chest wordmark"></div><div class="pname">Product Name</div><div class="stars">★★★★☆</div><div class="price">$120.00</div></article>

  <article class="card" style="left:119px;top:773px"><div class="shot pair-white" role="img" aria-label="Black and white tees pair"></div><div class="pname">Product Name</div><div class="stars">★★★★☆</div><div class="price">$120.00</div></article>
  <article class="card" style="left:366px;top:773px"><div class="shot teal" role="img" aria-label="Teal tee with lettered front print"></div><div class="pname">Product Name</div><div class="stars">★★★★☆</div><div class="price">$120.00</div></article>
  <article class="card" style="left:613px;top:773px"><div class="shot pair-purple" role="img" aria-label="Black and purple tees pair"></div><div class="pname">Product Name</div><div class="stars">★★★★☆</div><div class="price">$120.00</div></article>
  <article class="card" style="left:860px;top:773px"><div class="shot black" role="img" aria-label="Black tee with blue chest wordmark"></div><div class="pname">Product Name</div><div class="stars">★★★★☆</div><div class="price">$120.00</div></article>

  <article class="card" style="left:119px;top:1124px"><div class="shot black" role="img" aria-label="Black tee with lettered front print"></div><div class="pname">Product Name</div><div class="stars">★★★☆☆</div><div class="price">$120.00</div></article>
  <article class="card" style="left:366px;top:1124px"><div class="shot black" role="img" aria-label="Black tee with blue chest wordmark"></div><div class="pname">Product Name</div><div class="stars">★★★★☆</div><div class="price">$120.00</div></article>
  <article class="card" style="left:613px;top:1124px"><div class="shot white" role="img" aria-label="Two white tees with heart print"></div><div class="pname">Product Name</div><div class="stars">★★★★★</div><div class="price">$120.00</div></article>
  <article class="card" style="left:860px;top:1124px"><div class="shot black" role="img" aria-label="Black tee with purple chest wordmark"></div><div class="pname">Product Name</div><div class="stars">★★★★☆</div><div class="price">$120.00</div></article>
</main>

<nav class="pager">
  <span class="pg nav-btn"><svg width="10" height="10" viewBox="0 0 10 10" fill="none" stroke="#333" stroke-width="1.6"><path d="M6.5 1.5 3 5l3.5 3.5"/></svg></span>
  <span class="pg">1</span><span class="pg current">2</span><span class="pg">3</span><span class="pg">4</span>
  <span class="pg nav-btn"><svg width="10" height="10" viewBox="0 0 10 10" fill="none" stroke="#333" stroke-width="1.6"><path d="M3.5 1.5 7 5 3.5 8.5"/></svg></span>
</nav>

<section class="gallery">
  <h2 class="gallery-title">Snapshot</h2>
  <p class="gallery-lede">Meet your fellow Humans! Show us your UML style on Chirper, Snapshot or Friendbook and tag @UML for a chance to win free tees and be featured on our site!</p>
  <div class="photo" role="img" aria-label="Purple tee on a dark slate backdrop" style="left:255px;top:1720px;width:318px;height:294px;background:radial-gradient(circle at 50% 48%,#6d4fa0 0 32%,#373d46 33%)"></div>
  <div class="photo" role="img" aria-label="Person posing by a rock wall under blue sky" style="left:585px;top:1720px;width:179px;height:142px;background:linear-gradient(160deg,#6fb4d6,#5a6068)"></div>
  <div class="photo" role="img" aria-label="Person in a black hoodie in a dry field" style="left:774px;top:1720px;width:172px;height:142px;background:linear-gradient(180deg,#e8e6e2,#8f7c63)"></div>
  <div class="photo" role="img" aria-label="Person in white tee on a phone against a grey wall" style="left:585px;top:1873px;width:179px;height:141px;background:linear-gradient(150deg,#6d737a,#3f4449)"></div>
  <div class="photo" role="img" aria-label="Person in a black hoodie sitting on a boardwalk" style="left:774px;top:1873px;width:172px;height:141px;background:linear-gradient(180deg,#cfd8de,#8a857c)"></div>
</section>

<section class="newsletter">
  <h2 class="news-title">Join Our Newsletter</h2>
  <p class="news-sub">Sale up to 20% off for your next purchase in this month!</p>
  <div class="news-field"><span class="ph">Your email address</span><span class="btn">Subscribe</span></div>
</section>

<footer class="footer">
  <div class="fcol" style="left:154px"><h4>Contact Us</h4><p>Lorem Ipsum, is simply<br>dummy text of the</p><p>+xxx xxxx xxxxx</p><p>xxxxxxx@lantern.mail</p></div>
  <div class="fdiv" style="left:403px"></div>
  <div class="fcol" style="left:530px"><h4>Contact Us</h4><ul><li>Home</li><li>About</li><li>Services</li><li>Contact</li><li>Track Order</li></ul></div>
  <div class="fdiv" style="left:734px"></div>
  <div class="fbrand">U.M.L.<small>UNDER MORNING LANTERN</small></div>
  <div class="social"><span>Chirper</span><span>Circles</span><span>Friendbook</span><span>Reelhub</span></div>
</footer>

</body>
</html>
```